Business Card Design

We are a manufacturing and distribution company with most of our customer base being supermarkets. We have established brand guidelines that are attached.

```html
<!DOCTYPE html>
<html lang="en">
<head>
<meta charset="utf-8">
<title>Korvale Business Card</title>
<link rel="stylesheet" href="https://fonts.googleapis.com/css2?family=Montserrat:wght@600;700;800&family=Open+Sans:wght@400;600&display=swap">
<style>
  :root {
    --stage: #bdbdbd;
    --card-white: #ffffff;
    --ink: #1b1b1b;
    --ink-soft: #333333;
    --brand-red: #e0232b;
    --brand-blue: #0e64b4;
    --brand-blue-light: #2a82cf;
    --brand-blue-deep: #0b4f93;
    --rule-blue: #4a90d0;
  }
  * { box-sizing: border-box; margin: 0; padding: 0; }
  html, body { width: 1200px; height: 788px; overflow: hidden; }
  body {
    background: var(--stage);
    position: relative;
    font-family: "Open Sans", Arial, sans-serif;
  }
  .card {
    position: absolute;
    border-radius: 22px;
    box-shadow: 0 6px 18px rgba(0,0,0,0.18);
    overflow: hidden;
  }
  /* Front */
  .card-front {
    left: 170px; top: 114px;
    width: 340px; height: 556px;
    background: var(--card-white);
    display: flex; flex-direction: column; align-items: center;
    padding-top: 110px;
  }
  .brand {
    display: flex; align-items: center; gap: 12px;
  }
  .brand-square {
    width: 26px; height: 26px;
    background: var(--brand-red);
  }
  .brand-name {
    font-family: "Montserrat", Arial, sans-serif;
    font-weight: 800;
    font-size: 36px;
    letter-spacing: 1px;
    color: var(--ink);
  }
  .person { margin-top: 74px; text-align: center; }
  .person-name {
    font-family: "Montserrat", Arial, sans-serif;
    font-weight: 700;
    font-size: 25px;
    letter-spacing: 0.5px;
  }
  .person-name .first { color: var(--brand-red); }
  .person-name .last { color: var(--brand-blue); }
  .person-title {
    font-size: 13px; color: var(--ink-soft); margin-top: 2px;
  }
  .icon-row {
    margin-top: 18px;
    display: flex; align-items: center; gap: 6px;
    width: 250px;
  }
  .icon-row .rule { flex: 1; height: 1px; background: var(--rule-blue); }
  .icon {
    width: 24px; height: 24px; border-radius: 4px;
    background: var(--brand-red);
    display: flex; align-items: center; justify-content: center;
  }
  .contact {
    margin-top: 10px; text-align: center;
    font-size: 14px; line-height: 21px; color: var(--ink-soft);
  }
  .divider {
    width: 250px; height: 1px; background: var(--rule-blue);
    margin-top: 12px;
  }
  .address {
    margin-top: 12px; text-align: center;
    font-size: 14px; line-height: 21px; color: var(--ink-soft);
  }
  /* Back */
  .card-back {
    left: 560px; top: 224px;
    width: 556px; height: 340px;
  }
  .back-pattern {
    position: absolute; inset: 0;
    background: linear-gradient(135deg, var(--brand-blue-light) 0%, var(--brand-blue) 50%, var(--brand-blue-deep) 100%);
  }
  .back-brand {
    position: absolute; left: 50%; top: 50%;
    transform: translate(-50%, -50%);
    display: flex; align-items: center; gap: 8px;
  }
  .back-brand .brand-square { width: 16px; height: 16px; }
  .back-brand .brand-name { font-size: 20px; color: var(--card-white); }
</style>
</head>
<body>

  <section class="card card-front" aria-label="Business card front">
    <div class="brand">
      <span class="brand-square"></span>
      <span class="brand-name">KORVALE</span>
    </div>

    <div class="person">
      <h1 class="person-name"><span class="first">DELAN</span> <span class="last">MARSH</span></h1>
      <p class="person-title">CEO/Founder</p>
    </div>

    <div class="icon-row">
      <span class="rule"></span>
      <span class="icon" aria-label="Phone">
        <svg width="14" height="14" viewBox="0 0 24 24"><path fill="#fff" d="M6.6 10.8a15 15 0 0 0 6.6 6.6l2.2-2.2a1 1 0 0 1 1-.25 11.4 11.4 0 0 0 3.6.6 1 1 0 0 1 1 1V20a1 1 0 0 1-1 1A17 17 0 0 1 3 4a1 1 0 0 1 1-1h3.5a1 1 0 0 1 1 1c0 1.25.2 2.45.6 3.6a1 1 0 0 1-.25 1z"/></svg>
      </span>
      <span class="icon" aria-label="Email">
        <svg width="15" height="12" viewBox="0 0 24 18"><rect x="1" y="1" width="22" height="16" rx="1" fill="none" stroke="#fff" stroke-width="2"/><path d="M1 2l11 8 11-8" fill="none" stroke="#fff" stroke-width="2"/></svg>
      </span>
      <span class="icon" aria-label="Website">
        <svg width="14" height="14" viewBox="0 0 24 24"><circle cx="12" cy="12" r="10" fill="none" stroke="#fff" stroke-width="2"/><ellipse cx="12" cy="12" rx="4" ry="10" fill="none" stroke="#fff" stroke-width="1.6"/><path d="M2 12h20" stroke="#fff" stroke-width="1.6"/></svg>
      </span>
      <span class="rule"></span>
    </div>

    <p class="contact">
      +61 400 512 846<br>
      info@korvale.com.au<br>
      www.korvale.com.au
    </p>

    <div class="divider"></div>

    <p class="address">
      2281 Harbour Road Suite 14<br>
      Eastfield, TN 30418
    </p>
  </section>

  <section class="card card-back" aria-label="Business card back">
    <div class="back-pattern" role="img" aria-label="Repeating brand pattern in tones of blue"></div>
    <div class="back-brand">
      <span class="brand-square"></span>
      <span class="brand-name">KORVALE</span>
    </div>
  </section>

</body>
</html>
```